Hip surgeon needs a educative book cover design

I need to re-design my old book cover for its 3rd edition.
It's a small book dedicated to my patients, who underwent total hip replacement. It's meant to help people getting around the basic care after a total hip replacement surgery and getting back to their normal, active life.
The title is: "Morning light rituals: a quiet companion".
I already had a new logo, new stationery and new website design from ArtFolio (please see the attachments).
The final design should be look alike the other fresh new designs. It must communicate health, peacefulness.
I also attached the manual as it looks today for reference.
A5 size.
Just cover and back cover.
Health

```html
<!DOCTYPE html>
<html lang="en">
<head>
<meta charset="utf-8">
<title>Morning light rituals — cover and back cover</title>
<link rel="stylesheet" href="https://fonts.googleapis.com/css2?family=Fira+Sans:ital,wght@0,400;0,500;0,600;1,300;1,400&display=swap">
<style>
  :root {
    --bg: #ececea;
    --paper: #f4f3f0;
    --paper-front: #f7f7f6;
    --brand-blue: #1f6fb2;
    --title-blue: #2b67a3;
    --soft-blue: #b4c3dd;
    --text-soft: #8a97aa;
    --anatomy-red: #e8563a;
    --anatomy-bone: #ece7df;
    --anatomy-grey: #b9c6cf;
  }
  * { box-sizing: border-box; margin: 0; padding: 0; }
  html, body { width: 1200px; height: 1000px; overflow: hidden; }
  body {
    background: var(--bg);
    font-family: "Fira Sans", Arial, sans-serif;
    position: relative;
  }
  .cover {
    position: absolute;
    top: 200px;
    width: 420px;
    height: 594px;
    box-shadow: 0 10px 30px rgba(0,0,0,.12);
    overflow: hidden;
  }
  .back-cover { left: 150px; background: var(--paper); }
  .front-cover { left: 630px; background: var(--paper-front); }

  /* brand signature */
  .brand { display: flex; align-items: center; gap: 8px; position: absolute; }
  .brand-dot { width: 26px; height: 26px; border-radius: 50%; background: var(--brand-blue); flex: none; }
  .brand-text { color: var(--brand-blue); font-weight: 500; line-height: 1.1; }
  .brand-name { display: block; font-size: 17px; }
  .brand-tag { display: block; font-size: 13px; }

  /* back cover */
  .decor-circle {
    position: absolute; left: 50%; top: 92px;
    width: 300px; height: 300px; margin-left: -150px;
    border-radius: 50%; background: var(--soft-blue); opacity: .55;
  }
  .author-photo {
    position: absolute; left: 50%; top: 70px; margin-left: -45px;
    width: 90px; height: 118px;
    background: linear-gradient(180deg, #c9c4bb 0%, #e6e4e0 55%, #f2f2f2 100%);
  }
  .author-bio {
    position: absolute; left: 82px; top: 210px; width: 256px;
    font-style: italic; font-weight: 300; font-size: 10.5px; line-height: 1.45;
    color: var(--text-soft); text-align: justify;
  }
  .back-cover .brand { right: 24px; bottom: 22px; }
  .back-cover .brand-dot { width: 20px; height: 20px; }
  .back-cover .brand-name { font-size: 13px; }
  .back-cover .brand-tag { font-size: 10px; }

  /* front cover */
  .front-cover .brand { left: 22px; top: 32px; }
  .anatomy-art {
    position: absolute; left: 20px; top: 10px; width: 400px; height: 584px;
  }
  .cover-title {
    position: absolute; left: 0; width: 230px; bottom: 62px; text-align: center;
    color: var(--title-blue);
  }
  .cover-title h1 { font-size: 22px; font-weight: 600; }
  .cover-title .subtitle { font-size: 14px; font-weight: 400; opacity: .75; margin-top: 2px; }
  .cover-title .edition { font-size: 12px; font-style: italic; font-weight: 500; margin-top: 4px; }
</style>
</head>
<body>
  <section class="cover back-cover" aria-label="Back cover">
    <div class="decor-circle" aria-hidden="true"></div>
    <div class="author-photo" role="img" aria-label="Portrait photo of the author in a white coat"></div>
    <p class="author-bio">Physician trained at a regional federal university, specialist in orthopedics and traumatology with advanced training in hip surgery at home and abroad. Full member of the national orthopedic society, full member of the national hip society and member of an international academy of joint surgeons.</p>
    <div class="brand">
      <span class="brand-dot"></span>
      <span class="brand-text"><span class="brand-name">Dr. Elio R. Varano</span><span class="brand-tag">Cirurgia do Quadril</span></span>
    </div>
  </section>

  <section class="cover front-cover" aria-label="Front cover">
    <svg class="anatomy-art" viewBox="0 0 400 584" role="img" aria-label="Anatomical model of the hip joint and pelvis with coloured muscle attachments">
      <defs>
        <linearGradient id="artTone" x1="0" y1="0" x2="1" y2="1">
          <stop offset="0" stop-color="#f1eee9"/>
          <stop offset=".45" stop-color="#e6e1da"/>
          <stop offset=".7" stop-color="#e9b3a4"/>
          <stop offset="1" stop-color="#e8735a"/>
        </linearGradient>
      </defs>
      <path d="M140 0 H400 V584 H190 C200 500 215 420 170 360 C120 300 40 300 10 280 C20 220 100 160 140 100 Z" fill="url(#artTone)"/>
    </svg>
    <div class="brand">
      <span class="brand-dot"></span>
      <span class="brand-text"><span class="brand-name">Dr. Elio R. Varano</span><span class="brand-tag">Cirurgia do Quadril</span></span>
    </div>
    <div class="cover-title">
      <h1>Morning light rituals</h1>
      <p class="subtitle">- a quiet companion -</p>
      <p class="edition">- 3ª Edição -</p>
    </div>
  </section>
</body>
</html>
```